business card deign

Logo needs the following on it.
1. attached logo
2. Tagline - "If it keeps a drink cold or the party going...we do it!"
3. Name- Dalton Pikes, Founder and CPO
4. Address - 412 E. Carver Avenue, Ste 2207, Tampa, FL. 33917
5. Phone - 555.318.4726

```html
<!DOCTYPE html>
<html lang="en">
<head>
<meta charset="utf-8">
<title>Hoppwell — Business Card</title>
<link rel="stylesheet" href="https://fonts.googleapis.com/css2?family=Open+Sans:wght@400;600;800&display=swap">
<style>
  :root {
    --backdrop: #e6d3bd;
    --card: #ffffff;
    --ink: #111111;
    --ink-soft: #222222;
    --edge: #d2bfa8;
  }
  * { box-sizing: border-box; margin: 0; padding: 0; }
  html, body { width: 1200px; height: 711px; overflow: hidden; }
  body {
    background: var(--backdrop);
    font-family: "Open Sans", Arial, sans-serif;
    color: var(--ink);
    display: flex;
    align-items: center;
    justify-content: center;
    gap: 48px;
  }
  .card {
    position: relative;
    width: 532px;
    height: 304px;
    background: var(--card);
    border-radius: 24px;
    border: 1px solid var(--edge);
    overflow: hidden;
  }

  /* Front */
  .card--front {
    display: flex;
    align-items: center;
    justify-content: center;
  }
  .wordmark {
    display: flex;
    align-items: center;
    gap: 14px;
  }
  .wordmark__dot {
    width: 22px; height: 22px;
    border-radius: 50%;
    background: var(--ink);
  }
  .wordmark__name {
    font-weight: 800;
    letter-spacing: 0.22em;
    text-transform: uppercase;
    color: var(--ink);
  }
  .card--front .wordmark__name { font-size: 46px; }

  /* Back */
  .card--back .wordmark {
    position: absolute;
    top: 34px;
    right: 36px;
    gap: 8px;
  }
  .card--back .wordmark__dot { width: 12px; height: 12px; }
  .card--back .wordmark__name { font-size: 22px; }

  .details {
    position: absolute;
    top: 92px;
    right: 36px;
    width: 250px;
    font-size: 13px;
    line-height: 1.4;
    color: var(--ink-soft);
  }
  .details__tagline { margin-bottom: 12px; }
  .details__row {
    display: flex;
    align-items: flex-start;
    gap: 8px;
    margin-bottom: 4px;
  }
  .details__row svg { flex: none; width: 12px; height: 14px; margin-top: 3px; }

  .person {
    position: absolute;
    left: 36px;
    bottom: 32px;
  }
  .person__name {
    font-size: 26px;
    font-weight: 800;
    line-height: 1.1;
  }
  .person__role {
    font-size: 14px;
    font-weight: 400;
    margin-top: 2px;
  }
</style>
</head>
<body>

  <section class="card card--front" aria-label="Card front">
    <div class="wordmark">
      <span class="wordmark__dot"></span>
      <span class="wordmark__name">Hoppwell</span>
    </div>
  </section>

  <section class="card card--back" aria-label="Card back">
    <div class="wordmark">
      <span class="wordmark__dot"></span>
      <span class="wordmark__name">Hoppwell</span>
    </div>

    <div class="details">
      <p class="details__tagline">If it keeps a drink cold or<br>the party going...we do it!</p>
      <p class="details__row">
        <svg viewBox="0 0 12 14" aria-hidden="true"><path d="M3 1 L5 4 L3.8 5.4 Q5 8.4 7.6 10 L9 8.8 L11.5 10.8 L10 13 Q4 12.5 1.2 4 Q1 2 3 1 Z" fill="currentColor"/></svg>
        <span>555.318.4726</span>
      </p>
      <p class="details__row">
        <svg viewBox="0 0 12 14" aria-hidden="true"><path d="M6 0.5 A4.5 4.5 0 0 1 10.5 5 C10.5 8 6 13.5 6 13.5 C6 13.5 1.5 8 1.5 5 A4.5 4.5 0 0 1 6 0.5 Z M6 3.2 A1.8 1.8 0 1 0 6 6.8 A1.8 1.8 0 1 0 6 3.2 Z" fill="currentColor" fill-rule="evenodd"/></svg>
        <span>412 E. Carver Avenue,<br>Ste 2207, Tampa, FL. 33917</span>
      </p>
    </div>

    <div class="person">
      <p class="person__name">Dalton Pikes</p>
      <p class="person__role">Founder and CPO</p>
    </div>
  </section>

</body>
</html>
```